Communication and Marketing agency needs a new presentation card

We are a group of communication and marketing agencies specialized in companies that are in the logistics and industrial sector. The head agency is TELVANO Grupo and the group consists of 4 agencies: TELVANO Media, TELVANO Digital, TELVANO Research and DifundeEnPantalla. We hace 4 offices in Spain (Madrid, Barcelona, Valencia and Murcia). We are looking for a clean and attractive design that transmits our experience, brand presence in the market and knowledge to those who receive the card.It has to maintain the colors of the logo that is attached.
Target Market(s)
logistics and industrial sector
Marketing department
Contact Information for Business Card
Clean and attractive design

```html
<!DOCTYPE html>
<html lang="es">
<head>
<meta charset="utf-8">
<title>TELVANO Grupo – Tarjeta de presentación</title>
<link rel="stylesheet" href="https://fonts.googleapis.com/css2?family=Montserrat:wght@500&family=Roboto:wght@400;500;700&display=swap">
<style>
  :root {
    --page: #e4e4e4;
    --brand-red: #ad2428;
    --card-white: #ffffff;
    --charcoal: #524f4c;
    --ink-grey: #4f4c4a;
    --text-light: #ffffff;
  }
  * { margin: 0; padding: 0; box-sizing: border-box; }
  html, body {
    width: 1125px; height: 1200px; overflow: hidden;
    background: var(--page);
  }
  .canvas { position: relative; width: 1125px; height: 1200px; }

  .card {
    position: absolute; left: 183px; width: 800px; height: 456px;
    overflow: hidden;
  }
  .card--front { top: 121px; background: var(--card-white); }
  .card--back  { top: 638px; height: 458px; background: var(--charcoal); }

  .front__band { position: absolute; inset: 0; }

  .contact {
    position: absolute; left: 40px; top: 40px;
    color: var(--text-light);
    font-family: "Roboto", sans-serif;
  }
  .contact__name {
    font-family: "Montserrat", sans-serif; font-weight: 500;
    font-size: 25px; letter-spacing: 0.6px; line-height: 28px;
  }
  .contact__role { font-weight: 500; font-size: 19px; line-height: 24px; }
  .contact__list { list-style: none; margin-top: 14px; }
  .contact__item {
    display: flex; align-items: center; gap: 7px;
    font-size: 19.5px; line-height: 25.4px;
  }
  .contact__icon { width: 18px; height: 18px; flex: none; }
  .contact__offices { margin-top: 9px; font-size: 19.5px; }

  .front__logo {
    position: absolute; right: 53px; top: 300px;
    text-align: right; color: var(--brand-red);
    font-family: "Roboto", sans-serif; font-weight: 500;
  }
  .front__logo-main { font-size: 60px; line-height: 60px; letter-spacing: 2px; }
  .front__logo-sub { font-size: 36px; line-height: 44px; }

  .back__logo {
    position: absolute; left: 0; right: 0; top: 150px;
    text-align: center; color: var(--text-light);
    font-family: "Roboto", sans-serif; font-weight: 500;
  }
  .back__logo-main { font-size: 76px; line-height: 80px; letter-spacing: 3px; }
  .back__logo-sub { font-size: 44px; line-height: 54px; padding-left: 290px; }

  .agencies {
    position: absolute; left: 92px; right: 92px; top: 372px;
    display: flex; justify-content: space-between;
    color: var(--text-light);
    font-family: "Roboto", sans-serif; font-weight: 500;
  }
  .agency { text-align: right; }
  .agency__name { font-size: 21px; line-height: 22px; letter-spacing: 1px; }
  .agency__unit { font-size: 14px; line-height: 16px; }
  .agency--video { text-align: left; font-size: 17px; line-height: 20px; letter-spacing: 1px; }
</style>
</head>
<body>
<main class="canvas">

  <section class="card card--front" aria-label="Anverso de la tarjeta">
    <svg class="front__band" viewBox="0 0 800 456" aria-hidden="true">
      <polygon points="0,0 639,0 241,456 0,456" fill="var(--brand-red)"/>
    </svg>

    <div class="contact">
      <p class="contact__name">LORENZO VARELA</p>
      <p class="contact__role">Director</p>
      <ul class="contact__list">
        <li class="contact__item">
          <svg class="contact__icon" viewBox="0 0 24 24" aria-hidden="true"><path fill="#fff" d="M6.6 10.8a15.1 15.1 0 0 0 6.6 6.6l2.2-2.2c.3-.3.7-.4 1-.2 1.1.4 2.3.6 3.6.6.6 0 1 .4 1 1V20c0 .6-.4 1-1 1A17 17 0 0 1 3 4c0-.6.4-1 1-1h3.5c.6 0 1 .4 1 1 0 1.3.2 2.5.6 3.6.1.3 0 .7-.2 1z"/></svg>
          910 000 417
        </li>
        <li class="contact__item">
          <svg class="contact__icon" viewBox="0 0 24 24" aria-hidden="true"><rect x="6" y="2" width="12" height="20" rx="2" fill="none" stroke="#fff" stroke-width="2"/><circle cx="12" cy="18.5" r="1" fill="#fff"/></svg>
          600 482 135
        </li>
        <li class="contact__item">
          <svg class="contact__icon" viewBox="0 0 24 24" aria-hidden="true"><rect x="2" y="5" width="20" height="14" fill="#fff"/><path d="M2 5l10 8 10-8" fill="none" stroke="var(--brand-red)" stroke-width="1.6"/></svg>
          lvarela@telvano.es
        </li>
        <li class="contact__item">
          <svg class="contact__icon" viewBox="0 0 24 24" aria-hidden="true"><rect x="3" y="3" width="18" height="18" rx="2" fill="#fff"/></svg>
          lorenzovarela
        </li>
        <li class="contact__item">
          <svg class="contact__icon" viewBox="0 0 24 24" aria-hidden="true"><circle cx="12" cy="12" r="9" fill="none" stroke="#fff" stroke-width="2"/><path d="M3 12h18M12 3c3 3 3 15 0 18M12 3c-3 3-3 15 0 18" fill="none" stroke="#fff" stroke-width="1.5"/></svg>
          telvano.es
        </li>
      </ul>
      <p class="contact__offices">Madrid | Barcelona | Valencia | Murcia</p>
    </div>

    <div class="front__logo">
      <p class="front__logo-main">TELVANO</p>
      <p class="front__logo-sub">Media</p>
    </div>
  </section>

  <section class="card card--back" aria-label="Reverso de la tarjeta">
    <div class="back__logo">
      <p class="back__logo-main">TELVANO</p>
      <p class="back__logo-sub">Grupo</p>
    </div>

    <div class="agencies">
      <div class="agency">
        <p class="agency__name">TELVANO</p>
        <p class="agency__unit">Digital</p>
      </div>
      <div class="agency">
        <p class="agency__name">TELVANO</p>
        <p class="agency__unit">Media</p>
      </div>
      <div class="agency">
        <p class="agency__name">TELVANO</p>
        <p class="agency__unit">Research</p>
      </div>
      <div class="agency agency--video">
        <p>DIFUNDE</p>
        <p>ENPANTALLA</p>
      </div>
    </div>
  </section>

</main>
</body>
</html>
```